Theatre Company needs a Poster design for a world premiere of "The Lantern" Play.

We are premiering a play that celebrates community in rural and regional Australia . We need a poster for A3 and A5 size and an image that can be used in our email correspondence/webpage.

Attached is some ideas the producing theatre committee has come up with, a river runs through the town itself.

Town

```html
<!DOCTYPE html>
<html lang="en">
<head>
<meta charset="utf-8">
<title>The Lantern — Meridian Theatre Company</title>
<link rel="stylesheet" href="https://fonts.googleapis.com/css2?family=Oswald:wght@500&family=Pinyon+Script&display=swap">
<style>
  :root {
    --ink: #000000;
    --paper: #ffffff;
    --sky-dark: #1a1a1a;
    --sky-mid: #4a4a4a;
    --horizon: #d8d8d8;
    --hills: #202020;
    --water-light: #9a9a9a;
    --water-dark: #141414;
  }
  html, body {
    margin: 0;
    padding: 0;
    overflow: hidden;
    background: var(--ink);
  }
  .poster {
    position: relative;
    width: 939px;
    height: 1200px;
    background: var(--ink);
    color: var(--paper);
    overflow: hidden;
  }
  .company {
    position: absolute;
    top: 84px;
    left: 0;
    width: 100%;
    margin: 0;
    text-align: center;
    font-family: "Oswald", sans-serif;
    font-weight: 500;
    font-size: 40px;
    letter-spacing: 4px;
    line-height: 1;
  }
  .presents {
    position: absolute;
    top: 148px;
    left: 0;
    width: 100%;
    margin: 0;
    text-align: center;
    font-family: "Pinyon Script", cursive;
    font-size: 34px;
    letter-spacing: 10px;
    line-height: 1;
  }
  .scene {
    position: absolute;
    left: 106px;
    top: 252px;
    width: 728px;
    height: 676px;
    border-radius: 50%;
    background: linear-gradient(
      to bottom,
      var(--sky-dark) 0%,
      var(--sky-mid) 22%,
      var(--sky-dark) 30%,
      var(--horizon) 43%,
      var(--hills) 47%,
      var(--hills) 53%,
      var(--water-light) 60%,
      var(--sky-mid) 72%,
      var(--water-dark) 88%,
      var(--ink) 100%
    );
    box-shadow: inset 0 0 60px 40px var(--ink);
  }
  .title {
    position: absolute;
    top: 925px;
    left: 0;
    width: 100%;
    margin: 0;
    text-align: center;
    font-family: "Pinyon Script", cursive;
    font-weight: 400;
    font-size: 130px;
    line-height: 1.1;
  }
  .credit {
    position: absolute;
    top: 1080px;
    left: 0;
    width: 100%;
    margin: 0;
    text-align: center;
    font-family: "Pinyon Script", cursive;
    font-size: 30px;
    letter-spacing: 2px;
    line-height: 1;
  }
</style>
</head>
<body>
  <main class="poster">
    <p class="company">MERIDIAN THEATRE COMPANY</p>
    <p class="presents">Presents</p>
    <div class="scene" role="img" aria-label="Black-and-white photograph of a river winding between dark wooded hills under a stormy sky, framed in a soft oval"></div>
    <h1 class="title">The Lantern</h1>
    <p class="credit">Written by DELL MARSH</p>
  </main>
</body>
</html>
```